professional business card design for technology company

We are a small technology consulting firm, specialising in consulting based around Cloud and Managed services. Our colour scheme is yellow, blue and white, as you can see in the logos. Although we are based in melbourne australia, due to the nature of our work, our clients can be located anywhere. We are looking for a clean, professional, positive look - similar to our company logo

Target Market(s)

small business

Industry/Entity Type

Business

Contact Information for Business Card

eye catching, designed to incorporate some level of raised printing. Must contain website address, phone number, name and job title

Requirements
Must have
• Logo (attached) - use of the same colour scheme

```html
<!DOCTYPE html>
<html lang="en">
<head>
<meta charset="utf-8">
<title>Nuvoro business card</title>
<link rel="stylesheet" href="https://fonts.googleapis.com/css2?family=Open+Sans:wght@400;600;700;800&display=swap">
<style>
  :root {
    --backdrop: #e4e5e7;
    --card: #ffffff;
    --ink-grey: #4a4b4f;
    --band-grey: #5a5b5f;
    --sky-blue: #2fa6e0;
    --deep-blue: #1f2a6b;
    --text-light: #ffffff;
  }
  * { margin: 0; padding: 0; box-sizing: border-box; }
  html, body {
    width: 1200px; height: 772px; overflow: hidden;
    background: var(--backdrop);
    font-family: "Open Sans", Arial, sans-serif;
  }
  .canvas {
    position: relative; width: 1200px; height: 772px;
    display: flex; align-items: center; justify-content: center; gap: 60px;
  }
  .card {
    position: relative; width: 540px; height: 309px;
    background: var(--card);
    box-shadow: 0 4px 14px rgba(0,0,0,.12);
    overflow: hidden;
  }
  /* Front */
  .card-front { display: flex; align-items: center; justify-content: center; }
  .wordmark {
    display: flex; align-items: center; gap: 14px;
    font-weight: 800; color: var(--ink-grey); letter-spacing: -0.5px;
  }
  .wordmark .dot { border-radius: 50%; background: var(--sky-blue); flex: none; }
  .card-front .wordmark { font-size: 64px; }
  .card-front .wordmark .dot { width: 58px; height: 58px; }
  /* Back */
  .card-back .wave { position: absolute; inset: 0; width: 100%; height: 100%; }
  .card-back .wordmark {
    position: absolute; top: 30px; right: 44px; font-size: 44px; gap: 10px;
  }
  .card-back .wordmark .dot { width: 38px; height: 38px; }
  .holder { position: absolute; left: 30px; top: 84px; line-height: 1.3; }
  .holder-name { font-size: 19px; font-weight: 700; color: var(--deep-blue); }
  .holder-role { font-size: 17px; font-weight: 400; color: var(--ink-grey); }
  .contact {
    position: absolute; right: 26px; bottom: 14px;
    list-style: none; text-align: right;
    color: var(--text-light); font-size: 11.5px; line-height: 16.5px;
  }
  .contact li { display: flex; justify-content: flex-end; align-items: center; gap: 6px; }
  .contact svg { width: 10px; height: 10px; flex: none; }
  .contact .no-icon { margin-right: 16px; }
</style>
</head>
<body>
<main class="canvas">
  <section class="card card-front" aria-label="Card front">
    <div class="wordmark"><span class="dot"></span><span>Nuvoro</span></div>
  </section>

  <section class="card card-back" aria-label="Card back">
    <svg class="wave" viewBox="0 0 540 309" preserveAspectRatio="none" aria-hidden="true">
      <path d="M0,150 C170,130 300,205 540,150" fill="none" stroke="var(--sky-blue)" stroke-width="3"/>
      <path d="M0,160 C170,140 300,215 540,160 L540,309 L0,309 Z" fill="var(--sky-blue)"/>
      <path d="M0,170 C170,150 300,225 540,170 L540,309 L0,309 Z" fill="var(--band-grey)"/>
    </svg>

    <div class="wordmark"><span class="dot"></span><span>Nuvoro</span></div>

    <div class="holder">
      <p class="holder-name">Marlo Keane-Ashby</p>
      <p class="holder-role">Consultant</p>
    </div>

    <ul class="contact">
      <li><span class="no-icon">214 9th floor, Quay</span></li>
      <li>
        <span>Harbour Lane VT</span>
        <svg viewBox="0 0 10 10"><path d="M5 0.5a3 3 0 0 1 3 3c0 2.3-3 6-3 6s-3-3.7-3-6a3 3 0 0 1 3-3z" fill="var(--text-light)"/><circle cx="5" cy="3.5" r="1.1" fill="var(--band-grey)"/></svg>
      </li>
      <li>
        <span>014 220 5371</span>
        <svg viewBox="0 0 10 10"><path d="M2 0.8l1.8 2.1-1 1.2c.6 1.2 1.5 2.1 2.7 2.7l1.2-1 2.1 1.8-.9 1.6C5 9 1 5 .4 1.7z" fill="var(--text-light)"/></svg>
      </li>
      <li>
        <span>014 220 5372</span>
        <svg viewBox="0 0 10 10"><rect x="2.5" y="0.5" width="5" height="9" rx="1" fill="var(--text-light)"/><rect x="3.4" y="1.6" width="3.2" height="5.6" fill="var(--band-grey)"/></svg>
      </li>
      <li>
        <span>hello@nuvoro.net</span>
        <svg viewBox="0 0 10 10"><rect x="0.5" y="2" width="9" height="6" fill="var(--text-light)"/><path d="M0.8 2.3L5 5.4l4.2-3.1" fill="none" stroke="var(--band-grey)" stroke-width="0.8"/></svg>
      </li>
      <li>
        <span>www.nuvoroconsult.net</span>
        <svg viewBox="0 0 10 10"><circle cx="5" cy="5" r="4.2" fill="none" stroke="var(--text-light)" stroke-width="1"/><path d="M0.8 5h8.4M5 0.8c-2 2.6-2 5.8 0 8.4M5 0.8c2 2.6 2 5.8 0 8.4" fill="none" stroke="var(--text-light)" stroke-width="0.8"/></svg>
      </li>
    </ul>
  </section>
</main>
</body>
</html>
```